Tech business card design

We need an amazing business card design for our new business 'Pexla' a marketing tech startup based in Sydney, Australia. We provide an online marketplace for businesses to search and buy advertising media, connect with service providers and learn more about marketing. We wish to communicate 'cool tech', reliability and professionalism and design based around our logo.

Target Market(s)

Business Owners

Contact Information for Business Card

Name
Position
Email Address
Website
Phone Number

Font styles to use
Other font styles liked:
• Avenir & Avenir Next

Colors

Designer to choose colors to be used in the design.

```html
<!DOCTYPE html>
<html lang="en">
<head>
<meta charset="utf-8">
<title>Pexla Business Card</title>
<link rel="stylesheet" href="https://fonts.googleapis.com/css2?family=Arimo:wght@400;700&display=swap">
<style>
  :root {
    --navy: #1b1f4d;
    --fold-grey: #6c6d71;
    --card-white: #ffffff;
    --back-grey: #6f7073;
    --ink: #1a1a1a;
    --stage: #2a2a2c;
  }
  * { margin: 0; padding: 0; box-sizing: border-box; }
  html, body {
    width: 1200px; height: 803px; overflow: hidden;
    background: var(--stage);
    font-family: "Arimo", Arial, sans-serif;
  }
  .stage {
    position: relative; width: 1200px; height: 803px;
    display: flex; align-items: center; justify-content: center; gap: 80px;
  }
  .card {
    position: relative; width: 520px; height: 297px; overflow: hidden;
    box-shadow: 0 10px 30px rgba(0,0,0,0.45);
  }
  .card-front { background: var(--card-white); }
  .card-back { background: var(--back-grey); display: flex; align-items: center; justify-content: center; }

  .corner-art { position: absolute; inset: 0; width: 520px; height: 297px; }
  .corner-art .band { fill: var(--navy); }
  .corner-art .fold { fill: var(--fold-grey); }

  .holder {
    position: absolute; top: 10px; right: 18px; text-align: right; color: var(--card-white);
  }
  .holder-name { font-weight: 700; font-size: 14px; letter-spacing: 0.3px; }
  .holder-role { font-weight: 700; font-size: 10px; margin-top: 2px; }

  .wordmark {
    position: absolute; left: 26px; top: 92px;
    font-weight: 700; font-size: 62px; color: var(--navy); letter-spacing: -1px; line-height: 1;
  }
  .wordmark-large { font-weight: 700; font-size: 120px; color: var(--navy); letter-spacing: -2px; line-height: 1; }

  .address {
    position: absolute; left: 26px; top: 190px; font-size: 12px; line-height: 1.3; color: var(--ink);
  }
  .contacts {
    position: absolute; left: 30px; top: 228px; list-style: none; font-size: 12px; color: var(--ink);
  }
  .contacts li { display: flex; align-items: center; gap: 9px; height: 19px; }
  .contacts svg { width: 11px; height: 11px; fill: var(--ink); }
</style>
</head>
<body>
<main class="stage">
  <section class="card card-front" aria-label="Business card front">
    <svg class="corner-art" viewBox="0 0 520 297" aria-hidden="true">
      <path class="band" d="M178,0 H520 V58 H456 L192,20 Z"/>
      <path class="fold" d="M192,20 L456,58 C453,82 462,100 478,114 Z"/>
    </svg>
    <div class="holder">
      <p class="holder-name">JOHN SMITH</p>
      <p class="holder-role">Position</p>
    </div>
    <p class="wordmark">Pexla</p>
    <address class="address" style="font-style:normal">
      Street Name, City Name<br>Zipcode:012345
    </address>
    <ul class="contacts">
      <li>
        <svg viewBox="0 0 24 24" aria-hidden="true"><path d="M6.6 10.8a15 15 0 0 0 6.6 6.6l2.2-2.2c.3-.3.7-.4 1-.2 1.1.4 2.3.6 3.6.6.6 0 1 .4 1 1V20c0 .6-.4 1-1 1A17 17 0 0 1 3 4c0-.6.4-1 1-1h3.5c.6 0 1 .4 1 1 0 1.3.2 2.5.6 3.6.1.3 0 .7-.2 1z"/></svg>
        012-345-6789
      </li>
      <li>
        <svg viewBox="0 0 24 24" aria-hidden="true"><path d="M2 5h20v14H2z M4 7v.5l8 5 8-5V7l-8 5z" fill-rule="evenodd"/></svg>
        info@pexla.com
      </li>
      <li>
        <svg viewBox="0 0 24 24" aria-hidden="true"><path d="M12 2a10 10 0 1 0 0 20 10 10 0 0 0 0-20zm6.9 6h-3a15 15 0 0 0-1.3-3.9A8 8 0 0 1 18.9 8zM12 4c.8 1.2 1.5 2.5 1.9 4h-3.8c.4-1.5 1.1-2.8 1.9-4zM4.3 14a8 8 0 0 1 0-4h3.4a16 16 0 0 0 0 4zm.8 2h3a15 15 0 0 0 1.3 3.9A8 8 0 0 1 5.1 16zm3-8h-3a8 8 0 0 1 4.3-3.9C8.8 5.3 8.4 6.6 8.1 8zM12 20c-.8-1.2-1.5-2.5-1.9-4h3.8c-.4 1.5-1.1 2.8-1.9 4zm2.3-6H9.7a14 14 0 0 1 0-4h4.6a14 14 0 0 1 0 4zm.3 5.9c.6-1.2 1-2.5 1.3-3.9h3a8 8 0 0 1-4.3 3.9zM16.3 14a16 16 0 0 0 0-4h3.4a8 8 0 0 1 0 4z"/></svg>
        www.pexla.com
      </li>
    </ul>
  </section>

  <section class="card card-back" aria-label="Business card back">
    <p class="wordmark-large">Pexla</p>
  </section>
</main>
</body>
</html>
```